Business Card Design

Company is a Commercial Building Company specialising in New Construction and existing refurbishments

Industry/Entity Type

Business

Contact Information for Business Card

Liam Porter
Construction Manager
E Liam@marshbuilding.com.au
M 0400 213 594
Mail 14 Tarrant Rise Kelmore Bay WA 6097

```html
<!DOCTYPE html>
<html lang="en">
<head>
<meta charset="utf-8">
<title>Marsh Building &amp; Construction – Business Card</title>
<link rel="stylesheet" href="https://fonts.googleapis.com/css2?family=Roboto:wght@300;400;700&display=swap">
<style>
  :root {
    --canvas: #e6e7ea;
    --card-white: #ffffff;
    --navy: #1f2a44;
    --cyan: #1fb3dc;
    --orange: #f07f12;
    --text-grey: #3a3d44;
    --photo-faint-a: #f4f5f6;
    --photo-faint-b: #dfe2e5;
    --sky: #7cc3ea;
    --house-grey: #5b5f66;
  }
  * { margin: 0; padding: 0; box-sizing: border-box; }
  html, body {
    width: 1200px; height: 960px; overflow: hidden;
    background: var(--canvas);
    font-family: "Roboto", Arial, sans-serif;
  }
  .stage { position: relative; width: 1200px; height: 960px; }
  .card {
    position: absolute; left: 250px;
    width: 700px; height: 400px;
    background: var(--card-white);
    overflow: hidden;
    box-shadow: 0 6px 20px rgba(0,0,0,.18);
  }
  .card--front { top: 60px; }
  .card--back  { top: 500px; }

  .card__photo { position: absolute; inset: 0; }

  .brand {
    position: absolute; display: flex; align-items: center; gap: 14px;
    color: var(--navy); font-weight: 700; text-transform: uppercase;
    line-height: 1.1; white-space: nowrap;
  }
  .brand__square { width: 46px; height: 46px; background: var(--cyan); flex: none; }
  .brand__name { display: block; font-size: 20px; letter-spacing: .5px; }
  .brand__line { display: block; }

  .card--front .brand { left: 50%; top: 50%; transform: translate(-50%, -50%); gap: 18px; }
  .card--front .brand__square { width: 72px; height: 72px; }
  .card--front .brand__name { font-size: 32px; }

  .card--back .card__art { position: absolute; inset: 0; }
  .card--back .brand { left: 330px; top: 40px; }

  .contact { position: absolute; left: 330px; top: 136px; color: var(--text-grey); white-space: nowrap; }
  .contact__name { font-size: 40px; font-weight: 300; color: var(--orange); line-height: 1; }
  .contact__role { font-size: 14px; margin-top: 6px; }
  .contact__list { list-style: none; margin-top: 34px; font-size: 16px; line-height: 1.7; }
</style>
</head>
<body>
<main class="stage">

  <section class="card card--front">
    <svg class="card__photo" width="700" height="400" role="img" aria-label="Faded photograph of a modern two-storey house">
      <defs>
        <linearGradient id="faint" x1="0" y1="0" x2="0" y2="1">
          <stop offset="0" stop-color="var(--photo-faint-a)"/>
          <stop offset="1" stop-color="var(--photo-faint-b)"/>
        </linearGradient>
      </defs>
      <rect width="700" height="400" fill="url(#faint)"/>
    </svg>
    <div class="brand">
      <span class="brand__square"></span>
      <span class="brand__name"><span class="brand__line">Marsh Building</span><span class="brand__line">&amp; Construction</span></span>
    </div>
  </section>

  <section class="card card--back">
    <svg class="card__art" width="700" height="400" viewBox="0 0 700 400">
      <defs>
        <linearGradient id="house" x1="0" y1="0" x2="0" y2="1">
          <stop offset="0" stop-color="var(--sky)"/>
          <stop offset=".45" stop-color="var(--house-grey)"/>
          <stop offset="1" stop-color="#3e4046"/>
        </linearGradient>
      </defs>
      <rect width="700" height="400" fill="url(#house)" role="img" aria-label="Photograph of a modern grey house with a car in the driveway"/>
      <circle cx="520" cy="60" r="345" fill="var(--orange)"/>
      <circle cx="540" cy="50" r="340" fill="var(--card-white)"/>
    </svg>
    <div class="brand">
      <span class="brand__square"></span>
      <span class="brand__name"><span class="brand__line">Marsh Building</span><span class="brand__line">&amp; Construction</span></span>
    </div>
    <div class="contact">
      <p class="contact__name">Liam Porter</p>
      <p class="contact__role">Construction Manager</p>
      <ul class="contact__list">
        <li>0400 213 594</li>
        <li>Liam@marshbuilding.com.au</li>
        <li>14 Tarrant Rise Kelmore Bay WA 6097</li>
      </ul>
    </div>
  </section>

</main>
</body>
</html>
```